All-Natural Head Lice Removal company

I need a business card with my pre-existing logo. We are a new company located in Portland Oregon that goes into peoples homes to help with head lice removal. My products and approach are all- natural and also will be around children.On my current logo we used Teal Bl and the color Green. I am open to new ideas just want it simple and creative

Target Market(s)

my biggest market is families of school aged children

Industry/Entity Type

Business

Contact Information for Business Card

see upload for details from previous business card

Font styles to use
Serif

Colors
33a6d7
9bcb3b
f37122

Requirements
Must have
• Basic information/ logo put into a creative format that is catching to the eye
Nice to have
• creative

```html
<!DOCTYPE html>
<html lang="en">
<head>
<meta charset="utf-8">
<title>Nit Scout – Business Card</title>
<link href="https://fonts.googleapis.com/css2?family=Roboto+Slab:wght@400;700&display=swap" rel="stylesheet">
<style>
  :root {
    --teal: #33a6d7;
    --green: #9bcb3b;
    --green-deep: #6bb02c;
    --ink: #2b2b2b;
    --paper: #ffffff;
    --backdrop: #ecebe8;
  }
  * { margin: 0; padding: 0; box-sizing: border-box; }
  html, body { width: 1200px; height: 913px; overflow: hidden; }
  body {
    background: var(--backdrop);
    font-family: "Roboto Slab", serif;
    position: relative;
  }
  .card {
    position: absolute;
    width: 540px;
    height: 309px;
    background: var(--paper);
    border-radius: 14px;
    overflow: hidden;
    box-shadow: 0 6px 18px rgba(0,0,0,0.12);
  }
  .card--front { left: 40px; top: 150px; }
  .card--back { left: 620px; top: 454px; }

  .front-wave { position: absolute; inset: 0; }

  .brand {
    display: flex;
    align-items: center;
    gap: 10px;
    position: absolute;
  }
  .brand__dot {
    border-radius: 50%;
    background: var(--green);
    flex: none;
  }
  .brand__name {
    color: var(--ink);
    font-weight: 700;
    white-space: nowrap;
  }
  .card--front .brand { left: 30px; top: 128px; }
  .card--front .brand__dot { width: 34px; height: 34px; }
  .card--front .brand__name { font-size: 30px; }

  .holder {
    position: absolute;
    right: 26px;
    top: 22px;
    text-align: right;
  }
  .holder__name {
    font-size: 19px;
    letter-spacing: 1px;
    color: var(--ink);
  }
  .holder__role {
    font-size: 11px;
    color: var(--green);
    letter-spacing: 0.5px;
  }
  .holder__tagline {
    font-size: 13px;
    color: var(--teal);
    margin-top: 2px;
  }

  .contact {
    position: absolute;
    right: 24px;
    top: 150px;
    list-style: none;
    text-align: right;
    color: var(--ink);
    font-size: 13.5px;
    line-height: 20px;
  }
  .contact li { display: flex; justify-content: flex-end; align-items: center; gap: 8px; }
  .contact svg { width: 11px; height: 11px; fill: none; stroke: var(--paper); stroke-width: 1.6; }

  .card--back .brand {
    left: 50%;
    top: 78px;
    transform: translateX(-50%);
  }
  .card--back .brand__dot { width: 44px; height: 44px; }
  .card--back .brand__name { font-size: 44px; }

  .back-copy {
    position: absolute;
    left: 0; right: 0;
    top: 186px;
    text-align: center;
  }
  .back-copy__line {
    color: var(--teal);
    font-size: 14px;
    line-height: 19px;
  }
  .back-copy__web {
    color: var(--ink);
    font-size: 13px;
    font-weight: 700;
    margin-top: 6px;
  }
  .card--back::after {
    content: "";
    position: absolute;
    left: 0; right: 0; bottom: 0;
    height: 4px;
    background: var(--teal);
  }
</style>
</head>
<body>

<section class="card card--front" aria-label="Business card front">
  <svg class="front-wave" viewBox="0 0 540 309" preserveAspectRatio="none" aria-hidden="true">
    <path d="M0,309 L0,292 C140,300 240,265 320,180 C395,100 465,72 540,66 L540,309 Z" fill="var(--green)"/>
    <path d="M60,300 C200,290 270,240 340,165 C400,102 460,80 520,74" fill="none" stroke="var(--paper)" stroke-width="2.5"/>
  </svg>

  <div class="holder">
    <p class="holder__name">MARLA QUINN</p>
    <p class="holder__role">OWNER</p>
    <p class="holder__tagline">All Natural In-Home Lice Removal Services</p>
  </div>

  <div class="brand">
    <span class="brand__dot"></span>
    <span class="brand__name">Nit Scout</span>
  </div>

  <ul class="contact">
    <li>1-855-555-NITS (6487)
      <svg viewBox="0 0 12 12"><path d="M3 1 L5 3.5 L4 5 C5 7 6 8 7.5 8.5 L9 7.5 L11 9.5 L9.5 11 C5 10.5 1.5 7 1 2.5 Z"/></svg>
    </li>
    <li>Marla@NitScout.com
      <svg viewBox="0 0 12 12"><rect x="1" y="2.5" width="10" height="7"/><path d="M1 2.5 L6 6.5 L11 2.5"/></svg>
    </li>
    <li>www.NitScout.com
      <svg viewBox="0 0 12 12"><circle cx="6" cy="6" r="5"/><path d="M1 6 H11 M6 1 C3.5 3.5 3.5 8.5 6 11 M6 1 C8.5 3.5 8.5 8.5 6 11"/></svg>
    </li>
  </ul>
</section>

<section class="card card--back" aria-label="Business card back">
  <div class="brand">
    <span class="brand__dot"></span>
    <span class="brand__name">Nit Scout</span>
  </div>
  <div class="back-copy">
    <p class="back-copy__line">Try Nit Scout Today and Be Lice Free Tomorrow!</p>
    <p class="back-copy__line">All Natural In-Home Lice Removal Services</p>
    <p class="back-copy__web">www.NitScout.com</p>
  </div>
</section>

</body>
</html>
```